VOMRA Pty Ltd Business Card

Looking for a simple yet eye-catching double-sided business card design using my company logo on one side and contact details on the other.

Target Market(s)

Government

Industry/Entity Type

Communication Systems Engineering

Contact Information for Business Card

VOMRA Pty Ltd

Requirements
Nice to have
• Would be great to have a QR code so details can be scanned into contacts

```html
<!DOCTYPE html>
<html lang="en">
<head>
<meta charset="utf-8">
<title>VOMRA Pty Ltd Business Card</title>
<link href="https://fonts.googleapis.com/css2?family=Montserrat:wght@400;700&display=swap" rel="stylesheet">
<style>
  :root {
    --backdrop: #dcdcd9;
    --card: #ffffff;
    --ink: #36434b;
    --band: #000000;
    --shadow: rgba(0,0,0,0.18);
  }
  * { margin: 0; padding: 0; box-sizing: border-box; }
  html, body { width: 1200px; height: 801px; overflow: hidden; }
  body {
    background: var(--backdrop);
    font-family: "Montserrat", sans-serif;
    color: var(--ink);
    display: flex;
    align-items: center;
    justify-content: center;
    gap: 40px;
  }
  .card {
    position: relative;
    width: 540px;
    height: 309px;
    background: var(--card);
    border-radius: 16px;
    overflow: hidden;
    box-shadow: 0 10px 28px var(--shadow);
  }
  .card-swoosh { position: absolute; inset: 0; }
  .brand-name {
    position: absolute;
    font-weight: 700;
    color: var(--ink);
    letter-spacing: 2px;
  }
  .card-front .brand-name { left: 34px; top: 128px; font-size: 40px; }
  .divider {
    position: absolute;
    left: 222px; top: 50px;
    width: 1.5px; height: 210px;
    background: var(--ink);
  }
  .contact {
    position: absolute;
    left: 242px; top: 56px;
    font-size: 12.5px;
    line-height: 1.45;
  }
  .contact-name { font-size: 20px; font-weight: 700; line-height: 1.1; letter-spacing: 0.5px; }
  .contact-role { font-size: 13px; margin-bottom: 14px; }
  .contact-line { display: flex; align-items: center; gap: 7px; }
  .contact-line svg { width: 11px; height: 11px; fill: var(--ink); flex: none; }
  .contact-address { margin-top: 14px; }
  .card-back .brand-name {
    left: 0; right: 0; top: 50%;
    transform: translateY(-50%);
    text-align: center;
    font-size: 72px;
    letter-spacing: 4px;
  }
</style>
</head>
<body>
  <section class="card card-front" aria-label="Card front with contact details">
    <svg class="card-swoosh" viewBox="0 0 540 309" aria-hidden="true">
      <path d="M508 0 Q488 190 410 309 L430 309 Q500 200 520 0 Z" fill="var(--ink)"/>
      <path d="M520 0 Q500 200 430 309 L540 309 L540 0 Z" fill="var(--band)"/>
    </svg>
    <div class="brand-name">VOMRA</div>
    <div class="divider"></div>
    <div class="contact">
      <div class="contact-name">DANIEL HART</div>
      <div class="contact-role">Managing Director</div>
      <div class="contact-line">
        <svg viewBox="0 0 24 24"><path d="M6.6 10.8a15 15 0 0 0 6.6 6.6l2.2-2.2c.3-.3.7-.4 1-.2 1.1.4 2.3.6 3.6.6.6 0 1 .4 1 1V20c0 .6-.4 1-1 1A17 17 0 0 1 3 4c0-.6.4-1 1-1h3.5c.6 0 1 .4 1 1 0 1.3.2 2.5.6 3.6.1.3 0 .7-.2 1z"/></svg>
        <span>987 654 321</span>
      </div>
      <div class="contact-line">
        <svg viewBox="0 0 24 24"><path d="M2 5h20v14H2z M2 5l10 8 10-8" fill="var(--ink)"/></svg>
        <span>admin@vomra.com.au</span>
      </div>
      <div class="contact-line">
        <svg viewBox="0 0 24 24"><circle cx="12" cy="12" r="10"/></svg>
        <span>www.vomra.com.au</span>
      </div>
      <div class="contact-address">14-16 Harlow Lane Westmere<br>NSW 2150 Australia</div>
    </div>
  </section>

  <section class="card card-back" aria-label="Card back with company name">
    <div class="brand-name">VOMRA</div>
  </section>
</body>
</html>
```